Corvane Capital Business Cards

These are professional business cards that are for my family office.
Put fake emails and phone numbers as of now until I finalize those components. This family office controls my families investments, assets, and future. The cards should be professional.
..
.
.
.
I just uploaded another variation of a logo I would like to see as a business card to I am inbeteen which logo to use

Target Market(s)

business

Industry/Entity Type

business

Contact Information for Business Card

Professional, wealth related, finance related.

Requirements
Must have
• Logo

```html
<!DOCTYPE html>
<html lang="en">
<head>
<meta charset="utf-8">
<title>Corvane Capital Business Cards</title>
<link rel="stylesheet" href="https://fonts.googleapis.com/css2?family=Cinzel:wght@500&family=Montserrat:wght@400;600&display=swap">
<style>
  :root {
    --backdrop: #e9e7e3;
    --card: #1b1f2b;
    --ink: #ffffff;
    --muted: #a9a9ab;
    --serif: "Cinzel", "Times New Roman", serif;
    --sans: "Montserrat", "Helvetica Neue", Arial, sans-serif;
  }
  * { margin: 0; padding: 0; box-sizing: border-box; }
  html, body { width: 900px; height: 1200px; overflow: hidden; }
  body { background: var(--backdrop); position: relative; font-family: var(--sans); color: var(--ink); }

  .card {
    position: absolute;
    background: var(--card);
    border-radius: 28px;
    box-shadow: 0 8px 18px rgba(0,0,0,0.25);
  }
  .card--front { left: 80px; top: 132px; width: 742px; height: 440px; }
  .card--back  { left: 78px; top: 640px; width: 744px; height: 438px; }

  .wordmark {
    position: absolute;
    font-family: var(--serif);
    font-weight: 500;
    color: var(--ink);
    white-space: nowrap;
    line-height: 1;
  }
  .card--front .wordmark { left: 36px; top: 70px; font-size: 40px; }
  .card--back .wordmark { left: 0; right: 0; top: 322px; text-align: center; font-size: 46px; }

  .holder { position: absolute; right: 48px; top: 54px; text-align: right; }
  .holder__name { font-weight: 600; font-size: 27px; color: var(--muted); line-height: 1.1; }
  .holder__role { font-size: 16px; color: var(--ink); margin-top: 2px; }

  .address { position: absolute; left: 38px; top: 268px; font-size: 16px; line-height: 21px; }

  .contacts { position: absolute; left: 36px; top: 328px; list-style: none; font-size: 16px; }
  .contacts li { display: flex; align-items: center; height: 28.5px; }
  .contacts svg { width: 16px; height: 16px; margin-right: 10px; fill: var(--ink); opacity: 0.85; }

  .emblem-ring { position: absolute; }
  .card--front .emblem-ring { left: 438px; top: 156px; }
  .card--back .emblem-ring { left: 262px; top: 76px; }
</style>
</head>
<body>

<section class="card card--front" aria-label="Business card front">
  <div class="wordmark">Corvane Capital</div>
  <div class="holder">
    <div class="holder__name">Marcus Ellery</div>
    <div class="holder__role">Owner</div>
  </div>
  <address class="address" style="font-style:normal">48 Linden Park Avenue<br>Ashford, NJ 07911 USA</address>
  <ul class="contacts">
    <li>
      <svg viewBox="0 0 24 24" aria-hidden="true"><path d="M6.6 10.8a15.1 15.1 0 0 0 6.6 6.6l2.2-2.2a1 1 0 0 1 1-.25 11.4 11.4 0 0 0 3.6.57 1 1 0 0 1 1 1V20a1 1 0 0 1-1 1A17 17 0 0 1 3 4a1 1 0 0 1 1-1h3.5a1 1 0 0 1 1 1c0 1.25.2 2.45.57 3.57a1 1 0 0 1-.25 1z"/></svg>
      (555)214-7730
    </li>
    <li>
      <svg viewBox="0 0 24 24" aria-hidden="true"><path d="M3 5h18v14H3z M3 5l9 7 9-7" fill="none" stroke="#fff" stroke-width="0"/><path d="M3 6.5V19h18V6.5l-9 6.5z M3.5 5h17L12 11z"/></svg>
      info@corvanecapital.com
    </li>
    <li>
      <svg viewBox="0 0 24 24" aria-hidden="true"><path d="M12 2a10 10 0 1 0 0 20 10 10 0 0 0 0-20zm6.9 9h-3a15 15 0 0 0-1.4-5.9A8 8 0 0 1 18.9 11zM12 4.1c.9 1.2 1.8 3.6 1.9 6.9h-3.8c.1-3.3 1-5.7 1.9-6.9zM9.5 5.1A15 15 0 0 0 8.1 11h-3a8 8 0 0 1 4.4-5.9zM5.1 13h3a15 15 0 0 0 1.4 5.9A8 8 0 0 1 5.1 13zm6.9 6.9c-.9-1.2-1.8-3.6-1.9-6.9h3.8c-.1 3.3-1 5.7-1.9 6.9zm2.5-1a15 15 0 0 0 1.4-5.9h3a8 8 0 0 1-4.4 5.9z"/></svg>
      www.corvanecapital.com
    </li>
  </ul>
  <svg class="emblem-ring" width="268" height="268" viewBox="0 0 268 268" aria-hidden="true">
    <circle cx="134" cy="134" r="130" fill="none" stroke="var(--ink)" stroke-width="5"/>
  </svg>
</section>

<section class="card card--back" aria-label="Business card back">
  <svg class="emblem-ring" width="220" height="220" viewBox="0 0 220 220" aria-hidden="true">
    <circle cx="110" cy="110" r="106" fill="none" stroke="var(--ink)" stroke-width="4.5"/>
  </svg>
  <div class="wordmark">Corvane Capital</div>
</section>

</body>
</html>
```